BUSINESS CARD DESIGN

NAME- DALE VORSKIN
PHONE NUMER - 555- 714-9082
EMAIL- OFFICE@TRV-GROUNDMAKRZ.COM
BACK OF CARD- SPEACIALIZES IN LAND CLEARING, FORESTRY MUCLHING AND EXCAVATION

Contact Information for Business Card

NAME- DALE VORSKIN PHONE NUMER - 555- 714-9082 EMAIL- OFFICE@TRV-GROUNDMAKRZ.COM BACK OF CARD- SPEACIALIZES IN LAND CLEARING , MUCLHING AND EXCAVATION

```html
<!DOCTYPE html>
<html lang="en">
<head>
<meta charset="utf-8">
<title>TRV Groundmakrz – Business Card</title>
<link rel="stylesheet" href="https://fonts.googleapis.com/css2?family=Krona+One&family=Poppins:wght@400&display=swap">
<style>
  :root{
    --stage:#1c1c1c;
    --gold:#e6a615;
    --paper:#ffffff;
    --ink:#0d0d0d;
    --rule:rgba(0,0,0,.35);
    --deco:#111111;
  }
  *{box-sizing:border-box;margin:0;padding:0}
  html,body{width:1200px;height:1015px;overflow:hidden}
  body{background:var(--stage);position:relative;font-family:"Poppins",sans-serif;color:var(--ink)}
  .card{position:absolute;left:230px;width:740px;height:423px;overflow:hidden;box-shadow:0 10px 30px rgba(0,0,0,.6)}
  .card--back{top:64px;background:var(--gold)}
  .card--front{top:528px;background:var(--paper)}
  .brand{position:absolute;left:50px;top:150px;width:270px;display:flex;align-items:center;gap:14px}
  .brand__dot{flex:none;width:42px;height:42px;border-radius:50%;background:var(--ink)}
  .brand__name{font-family:"Krona One",sans-serif;font-size:18px;line-height:1.3;letter-spacing:.4px;color:var(--ink);white-space:nowrap}
  .brand__name span{display:block}
  .divider{position:absolute;left:335px;top:110px;width:1px;height:200px;background:linear-gradient(transparent,var(--rule) 20%,var(--rule) 80%,transparent)}
  .panel{position:absolute;left:360px;top:125px}
  .panel__title{font-family:"Krona One",sans-serif;font-size:18px;letter-spacing:.5px;margin-bottom:20px;white-space:nowrap}
  .list{list-style:none}
  .list li{display:flex;align-items:center;gap:12px;height:44px;font-size:17px;text-transform:uppercase;letter-spacing:.3px;white-space:nowrap}
  .list--contact li{text-transform:none;font-size:17px;letter-spacing:0}
  .bullet{flex:none;width:30px;height:30px;border:2px solid var(--ink);border-radius:50%;display:flex;align-items:center;justify-content:center}
  .bullet svg{width:15px;height:15px}
  .palms{position:absolute;right:0;top:55px;width:95px;height:80px;background:linear-gradient(180deg,rgba(17,17,17,.85),var(--deco));border-radius:50px 0 0 0}
</style>
</head>
<body>

<section class="card card--back">
  <div class="brand"><span class="brand__dot"></span><span class="brand__name"><span>TRV</span><span>GROUNDMAKRZ</span><span>LLC</span></span></div>
  <div class="divider"></div>
  <div class="panel">
    <h2 class="panel__title">SPECIALIZES IN</h2>
    <ul class="list">
      <li><span class="bullet"></span>Land Clearing</li>
      <li><span class="bullet"></span>Mulching</li>
      <li><span class="bullet"></span>Excavation</li>
    </ul>
  </div>
  <div class="palms" role="img" aria-label="Silhouette of palm trees and an excavator"></div>
</section>

<section class="card card--front">
  <div class="brand"><span class="brand__dot"></span><span class="brand__name"><span>TRV</span><span>GROUNDMAKRZ</span><span>LLC</span></span></div>
  <div class="divider"></div>
  <div class="panel">
    <h2 class="panel__title">DALE VORSKIN</h2>
    <ul class="list list--contact">
      <li><span class="bullet"><svg viewBox="0 0 16 16"><path d="M3 1.5l3 3-1.5 2a8 8 0 0 0 5 5l2-1.5 3 3-2 2C6 14 2 10 1 3.5z" fill="none" stroke="currentColor" stroke-width="1.4"/></svg></span>555- 714-9082</li>
      <li><span class="bullet"><svg viewBox="0 0 16 16"><rect x="1.5" y="3.5" width="13" height="9" fill="none" stroke="currentColor" stroke-width="1.4"/><path d="M1.5 3.5l6.5 5 6.5-5" fill="none" stroke="currentColor" stroke-width="1.4"/></svg></span>office@trv-groundmakrz.com</li>
      <li><span class="bullet"><svg viewBox="0 0 16 16"><circle cx="8" cy="8" r="6.5" fill="none" stroke="currentColor" stroke-width="1.3"/><ellipse cx="8" cy="8" rx="3" ry="6.5" fill="none" stroke="currentColor" stroke-width="1.1"/><path d="M1.5 8h13M2.5 5h11M2.5 11h11" stroke="currentColor" stroke-width="1"/></svg></span>www.trv-groundmakrz.com</li>
    </ul>
  </div>
  <div class="palms" role="img" aria-label="Silhouette of palm trees and an excavator"></div>
</section>

</body>
</html>
```